Open Harbor book needs a cover design

I need a front and back cover design that demonstrates a strong sense of possibility that trust can be repaired even if things look bleak. Repairing trust is difficult, but this book is full of wisdom, proven strategies, and doctoral research to help people strengthen relationships and improve trust. It can help any group: business, nonprofit, education, service. Showing diversity of groups and people is very important. For the cover title, there should be a play on words: "Open Harbor: Is it? Within Reach" should have the words "is it?" crossed out and the words "It IS! should be replaced there in a striking way. Perhaps in red ink. For publishing purposes, book will be titled Open Harbor: It IS Within Reach! Please see the attachment for an example. The book layout is approximately 260 pages.

A business self-help book, but the target is any person in a group that feels they have lost trust in each other. It can be just a normal person struggling in a volunteer group they are a part of, or a supervisor whose group is not working well together. It can be a leader who just wants their group to be stronger.

Business Management

• Allise - I believe is being used on the interior of the book for the title page and headings

• Show hope and possibility in the midst of difficulty. Must have a play on the words in the title "Open Harbor: Is it? Within Reach" with crossing out "is it?" with "It IS!" (see attached example) Must include the author's name: Marla Quentin, PhD Must include a smaller tagline: "Practical Steps to Move Teams Forward Again"
• Showing diverse people, or hands. Diverse kinds of groups - not just business. A colorful cover. Maybe show the complexity of trust when it is broken...broken pieces of trust that are then picked up and put together when people work together. Could show people (or images of hands) or other ways to show that it's a choice and it is possible to repair broken trust. I'd also like to convey a sense of a group - not just random people. That they have something at stake to work on repairing trust together and this book can help them.
• If images of people are used, just showing one gender or race is not okay. Nor just binary choices: like an image containing one man and one woman, or one white person and one person of color - otherwise it seems that the book on Open Harbor is about race or gender relations.

```html
<!DOCTYPE html>
<html lang="en">
<head>
<meta charset="utf-8">
<title>Open Harbor: It IS Within Reach!</title>
<link href="https://fonts.googleapis.com/css2?family=Neucha&display=swap" rel="stylesheet">
<style>
  :root {
    --paper: #ffffff;
    --ink: #2a2926;
    --leaf: #6e9a2c;
    --strike: #e0242a;
    --bark-dark: #4a3a2c;
    --bark-mid: #8a7560;
  }
  html, body {
    margin: 0;
    padding: 0;
    overflow: hidden;
    background: var(--paper);
  }
  .cover {
    position: relative;
    width: 800px;
    height: 1200px;
    background: var(--paper);
    font-family: "Neucha", "Comic Sans MS", sans-serif;
    color: var(--ink);
    overflow: hidden;
  }
  .title {
    position: absolute;
    top: 70px;
    left: 0;
    width: 100%;
    margin: 0;
    text-align: center;
    font-weight: 400;
    line-height: 1;
  }
  .title-main {
    display: block;
    font-size: 112px;
    line-height: 1;
  }
  .title-struck {
    display: inline-block;
    position: relative;
    font-size: 82px;
    line-height: 1;
    margin-top: 4px;
  }
  .title-struck .strike-line {
    position: absolute;
    left: -6px;
    right: -8px;
    top: 46%;
    height: 7px;
    background: var(--strike);
    transform: rotate(-4deg);
  }
  .title-answer {
    display: block;
    font-size: 100px;
    line-height: 1;
    margin-top: 6px;
  }
  .title-answer .affirm {
    color: var(--leaf);
  }
  .hero-art {
    position: absolute;
    left: 150px;
    top: 440px;
    width: 500px;
    height: 440px;
  }
  .tagline {
    position: absolute;
    top: 900px;
    left: 0;
    width: 100%;
    margin: 0;
    text-align: center;
    color: var(--leaf);
    font-size: 44px;
    line-height: 1.25;
    font-weight: 400;
  }
  .author {
    position: absolute;
    top: 1092px;
    left: 0;
    width: 100%;
    margin: 0;
    text-align: center;
    font-size: 38px;
    font-weight: 400;
    color: var(--ink);
  }
</style>
</head>
<body>
  <main class="cover">
    <h1 class="title">
      <span class="title-main">Open Harbor:</span>
      <span class="title-struck">Is it?<span class="strike-line" aria-hidden="true"></span></span>
      <span class="title-answer"><span class="affirm">It is</span> Within Reach!</span>
    </h1>

    <svg class="hero-art" viewBox="0 0 500 440" role="img" aria-label="Photograph of a hollow, weathered tree stump with a young green sapling growing from inside it">
      <defs>
        <radialGradient id="stumpTone" cx="50%" cy="42%" r="60%">
          <stop offset="0%" stop-color="#3a5a22"/>
          <stop offset="22%" stop-color="#4a3a2c"/>
          <stop offset="60%" stop-color="#8a7560"/>
          <stop offset="100%" stop-color="#ffffff" stop-opacity="0"/>
        </radialGradient>
      </defs>
      <rect x="0" y="0" width="500" height="440" fill="url(#stumpTone)"/>
    </svg>

    <p class="tagline">Practical Steps to Move Teams<br>Forward Again</p>

    <p class="author">Marla Quentin, PhD</p>
  </main>
</body>
</html>
```